Header/Banner Design for Website

Looking for a banner/header design for www.nestfixerdiaries.net Should be fun and whimsical, and include the name of the website, something to do with home improvement or tools, and a caricature of a young, beautiful 20 something blond who the website revolves around. The website is about a young woman who bought her first house and it taking on all of the renovations and remodeling on her own for the first time.

The header/banner should include the same colors that are in the website. The width should be no more than 430 pixels, the height is flexible but the current space in the header is 85 pixels...looking for some creativity. any questions, please ask. Attached an image that she liked for the image of the woman (would like to see versions of this included)
Updates

Target Market(s)

women 20+ that are new home owners or that are tackling home improvement on their own

Industry/Entity Type

Home Improvement

Requirements
Must have
• color coordinate with the website
should feature a young, blond, female caricature
should include the name of the website

```html
<!DOCTYPE html>
<html lang="en">
<head>
<meta charset="utf-8">
<title>Nest Fixer Diaries — Header Banners</title>
<link rel="stylesheet" href="https://fonts.googleapis.com/css2?family=Teko:wght@500;600&family=Arimo:wght@400;700&display=swap">
<style>
  :root {
    --page: #ffffff;
    --ink: #111111;
    --pink: #d2368d;
    --pink-deep: #c22a7f;
    --skyline: #bb2878;
    --wordmark: #ffffff;
    --field: #fde4f6;
    --field-border: #e9b6d6;
    --button: #8c1b57;
    --button-text: #ffffff;
    --figure-hair: #f6e15a;
    --figure-dress: #c9a3d6;
  }
  html, body {
    margin: 0;
    width: 1200px;
    height: 382px;
    overflow: hidden;
    background: var(--page);
  }
  .sheet {
    position: relative;
    width: 1200px;
    height: 382px;
  }
  .size-label {
    position: absolute;
    left: 0;
    width: 1100px;
    text-align: center;
    font-family: "Teko", sans-serif;
    font-weight: 600;
    font-size: 38px;
    line-height: 1;
    color: var(--ink);
    margin: 0;
  }
  .size-label--small { top: 20px; }
  .size-label--wide { top: 185px; }

  .banner {
    position: absolute;
    height: 120px;
    overflow: hidden;
    background: linear-gradient(180deg, var(--pink) 0%, var(--pink-deep) 100%);
  }
  .banner--small { left: 335px; top: 52px; width: 430px; }
  .banner--wide { left: 48px; top: 217px; width: 1003px; }

  .skyline {
    position: absolute;
    left: 0;
    bottom: 0;
    width: 100%;
    height: 32px;
    background: var(--skyline);
    opacity: 0.75;
  }

  .wordmark {
    position: absolute;
    margin: 0;
    font-family: "Teko", sans-serif;
    font-weight: 500;
    color: var(--wordmark);
    line-height: 1;
    white-space: nowrap;
    letter-spacing: 0.5px;
  }
  .banner--small .wordmark { left: 46px; top: 44px; font-size: 42px; }
  .banner--wide .wordmark { left: 40px; top: 40px; font-size: 52px; }

  .figure {
    position: absolute;
    top: 0;
    height: 120px;
    background: linear-gradient(180deg, var(--figure-hair) 0%, var(--figure-hair) 45%, var(--figure-dress) 100%);
    border-radius: 40px 40px 0 0;
    opacity: 0.9;
  }
  .banner--small .figure { left: 345px; width: 85px; }
  .banner--wide .figure { left: 520px; width: 95px; }

  .search {
    position: absolute;
    left: 662px;
    top: 41px;
    width: 317px;
    height: 39px;
    display: flex;
  }
  .search__field {
    flex: 0 0 203px;
    box-sizing: border-box;
    border: 1px solid var(--field-border);
    background: var(--field);
    font-family: "Arimo", sans-serif;
    font-size: 13px;
    color: var(--ink);
    padding: 0 6px;
    display: flex;
    align-items: center;
  }
  .search__button {
    flex: 1;
    background: var(--button);
    color: var(--button-text);
    font-family: "Arimo", sans-serif;
    font-weight: 700;
    font-size: 17px;
    display: flex;
    align-items: center;
    justify-content: center;
    gap: 6px;
    border-radius: 0 3px 3px 0;
  }
</style>
</head>
<body>
  <main class="sheet">
    <h2 class="size-label size-label--small">430X120</h2>
    <section class="banner banner--small">
      <div class="skyline" role="img" aria-label="Pink city skyline silhouette"></div>
      <h1 class="wordmark">NEST FIXER DIARIES</h1>
      <div class="figure" role="img" aria-label="Caricature of a young blonde woman in a lilac top"></div>
    </section>

    <h2 class="size-label size-label--wide">1003X120</h2>
    <section class="banner banner--wide">
      <div class="skyline" role="img" aria-label="Pink city skyline silhouette"></div>
      <h1 class="wordmark">NEST FIXER DIARIES</h1>
      <div class="figure" role="img" aria-label="Caricature of a young blonde woman in a lilac top"></div>
      <div class="search">
        <span class="search__field">Search</span>
        <span class="search__button">Search
          <svg width="16" height="16" viewBox="0 0 16 16" aria-hidden="true">
            <circle cx="9.5" cy="6.5" r="4.5" fill="#ffffff"/>
            <line x1="6" y1="10" x2="2" y2="14" stroke="#ffffff" stroke-width="2.5" stroke-linecap="round"/>
          </svg>
        </span>
      </div>
    </section>
  </main>
</body>
</html>
```